Need Website Design for Non-Profit Veteran Site

I am looking for a very talented creative website designer for a modern feel. I'll give a little bit of guidance around what I am looking for and then your creative juices should kick in and design away. I have already purchased the domain but will need hosting (at least temporarily) and the creative design work done.The website domain is militarydocs.orgI am looking to attract current and veteran military providers (doctors, nurse practitioners, physician assistants, etc) to join and signup for membership. They would pay a yearly fee to join. Would need membership categories $135 for Provider, $55 Student, $100 for Retired, and Organization (Organization would be broken down into Less than 100 ($200), 100-249 ($250), 250-499 ($300), 500-999 ($400), 1,000-2,999 ($500), and 3,000 ($700). Would need Benefit built out and would need to accept money through CoinVane and other means. Since it's a new organization just starting, would also need a Donate button to get people to donate if they want any amount they would like. The second part of the website is that once they join, they will have acess to a list of all other providers who have registered within the website (not exportable) so they can connect with one another. If they want to see contact information this will be included in their fee as a benefit to socialize with one another. As part of the website, there will be another Veteran's portal so veterans who would like to connect with a provider around a particular speciality can reach out and request help from the doctor writing a nexus letter or letter to support the veteran who is filing a claim with the BQ. Veterans would pay a yearly sign-up fee of $30.00 and would need their membership benefits displayed. They would have access to a list of veterans in their region by state and distance, and can reach out to doctors to get their help. If a doctor and veteran agree, sharable inforamtion of medical hipaa documents can be exchanged via the website. The physician and veteran can negotiate a fee through the website only and share their details. This is a separate fee for this type of process between the provider and veteran. We will collect a $250 fee for admin on each of these and each project the veteran does with the provider will cost $450 (so essentially the doctor gets paid $450 and i get $250.00. This model could be changed over time as we start to test this out). A good example of 50% of what I'm looking for is something like the following website: https://www.lpkt.org/ It has some of the features but not all and my site should be more modernized to attract the veteran and military providers.

Target Market(s)

Current and retired military providers and veterans

Industry/Entity Type

Non Profit

Number of Pages Required

1 page

Requirements
Must have
• Military Design
• Modern Feel (Example templates for feel -https://quillmoth.com/free-photoshop-psd-web-design-template/)
• Donation box
• Stuff mentioned in the description)
Nice to have
• Open to feedback
Should not have
• Open to feedback

```html
<!DOCTYPE html>
<html lang="en">
<head>
<meta charset="utf-8">
<title>Harborwell Net</title>
<link rel="stylesheet" href="https://fonts.googleapis.com/css2?family=Oswald:wght@400;500;700&family=Lato:wght@400;700&display=swap">
<style>
:root{
  --olive:#516826;
  --olive-dark:#3f521c;
  --camo-light:#86ad3c;
  --camo-mid:#5f8a2a;
  --red:#d51717;
  --red-deep:#9a0d0d;
  --ink:#1b1b1b;
  --white:#ffffff;
  --title-green:#4a5f22;
  --text:#222;
}
*{box-sizing:border-box;margin:0;padding:0}
html,body{width:1200px;height:2308px;overflow:hidden}
body{position:relative;font-family:"Lato",sans-serif;background:var(--olive);color:var(--white)}
.abs{position:absolute}
.camo-top{left:0;top:0;width:1200px;height:900px;background:linear-gradient(180deg,var(--camo-light) 0,var(--camo-mid) 260px,var(--olive) 520px)}
.logo{left:77px;top:36px;font-family:"Oswald",sans-serif;font-weight:700;font-size:42px;color:var(--ink);letter-spacing:.5px}
.pill{top:34px;height:52px;border-radius:26px;background:var(--white);display:flex;align-items:center;font-family:"Oswald",sans-serif;font-size:26px;color:var(--ink);padding-left:6px;gap:12px}
.pill .dot{width:42px;height:42px;border-radius:50%;display:flex;align-items:center;justify-content:center}
.join{left:515px;width:157px}.join .dot{background:#3a3a3a}
.signup{left:690px;width:159px}.signup .dot{background:var(--red)}
.call-dot{left:869px;top:34px;width:52px;height:52px;border-radius:50%;background:var(--white);display:flex;align-items:center;justify-content:center}
.call-dot span{width:42px;height:42px;border-radius:50%;background:#5f8e2a;display:flex;align-items:center;justify-content:center}
.call-top{left:943px;top:30px;font-family:"Oswald",sans-serif}
.call-top .lbl{font-size:18px;font-weight:400}
.call-top .num{font-size:30px;font-weight:700;line-height:1.1}
.nav{left:75px;top:118px;width:1050px;height:59px;background:var(--ink);display:flex;align-items:center;padding-left:66px}
.nav a{font-family:"Oswald",sans-serif;font-size:15px;color:var(--white);text-decoration:none;margin-right:32px}
.search{position:absolute;right:15px;top:12px;width:146px;height:35px;background:#111;display:flex;align-items:center;justify-content:space-between;padding:0 12px;font-family:"Oswald",sans-serif;font-size:15px}
.hero-red{left:75px;top:177px;width:1050px;height:543px;background:linear-gradient(135deg,var(--red-deep),#c21616 55%,#8a0b0b)}
.hero-photo{left:75px;top:177px;width:580px;height:543px;background:linear-gradient(160deg,#eef1f3,#cfdcdf 60%,#2a8c8a);clip-path:polygon(0 0,580px 0,488px 100%,0 100%)}
.hero-title{left:669px;top:288px;font-family:"Oswald",sans-serif;font-weight:500;font-size:50px}
.hero-text{left:672px;top:374px;width:420px;font-size:19px;line-height:25px}
.btn{display:flex;align-items:center;justify-content:center;background:var(--red);color:var(--white);font-family:"Oswald",sans-serif;border-radius:30px;box-shadow:0 3px 0 rgba(0,0,0,.25)}
.donate{left:660px;top:477px;width:221px;height:54px;font-size:21px;font-weight:500}
.arrows{left:665px;top:563px}
.members{left:75px;top:720px;width:1050px;height:118px;background:var(--red);font-family:"Oswald",sans-serif}
.members .title{position:absolute;left:0;width:457px;top:40px;text-align:center;font-size:28px;font-weight:500}
.members .divider{position:absolute;left:457px;top:0;width:2px;height:118px;background:#b51010}
.tier{position:absolute;top:28px;text-align:center;transform:translateX(-50%);line-height:1.2}
.tier .n{font-size:16px;font-weight:500}
.tier .p{font-size:33px;font-weight:500}
.sec-title{width:1200px;left:0;text-align:center;font-family:"Oswald",sans-serif;font-size:38px;font-weight:400}
.sec-text{left:86px;width:1028px;text-align:center;font-size:14.5px;line-height:26px}
.small-btn{height:36px;font-size:14px;font-weight:500;border-radius:18px}
.veteran-bg{left:0;top:1061px;width:1200px;height:440px;background:linear-gradient(100deg,#1b1d17,#3a3d31 35%,#2b2d24 70%,#4c4f41);clip-path:polygon(0 0,1200px 77px,1200px 440px,0 362px)}
.white-sec{left:0;top:1423px;width:1200px;height:652px;background:var(--white);clip-path:polygon(0 0,1200px 77px,1200px 652px,0 652px)}
.col-title{font-family:"Oswald",sans-serif;font-size:38px;color:var(--title-green)}
.news-item{left:75px;width:504px;display:flex;align-items:flex-start;gap:27px}
.date{flex:none;width:90px;height:90px;border-radius:50%;background:var(--red);display:flex;flex-direction:column;align-items:center;justify-content:center;font-family:"Oswald",sans-serif;line-height:1}
.date .d{font-size:29px}.date .m{font-size:13px;margin-top:6px}
.news-item p{color:var(--text);font-size:17px;line-height:24px;text-align:justify;padding-top:4px}
.prog-photo{left:621px;top:1587px;width:502px;height:225px;background:linear-gradient(100deg,#dfe6ee,#b9c6d6 50%,#eef2f6);box-shadow:0 0 0 3px #e6e6e6}
.prog-text{left:621px;top:1834px;width:502px;color:var(--text);font-size:17px;line-height:24px;text-align:justify}
.contact-band{left:0;top:2075px;width:1200px;height:86px;background:var(--olive)}
.footer{left:0;top:2161px;width:1200px;height:147px;background:var(--ink)}
.foot-nav{left:77px;top:2188px;display:flex;gap:28px;font-family:"Oswald",sans-serif;font-size:14px}
.social{left:77px;top:2225px;display:flex;gap:20px}
.social span{width:16px;height:16px;border-radius:50%;background:var(--white)}
.copy{left:77px;top:2259px;font-size:11.5px;color:#ddd}
.foot-logo{left:966px;top:2209px;font-family:"Oswald",sans-serif;font-weight:700;font-size:24px;color:#8a8a8a}
.foot-mark{left:1154px;top:2260px;font-family:"Oswald",sans-serif;font-size:12px;font-weight:700}
</style>
</head>
<body>
<div class="abs camo-top" role="img" aria-label="Green military camouflage background"></div>

<header>
  <div class="abs logo">HARBORWELL NET</div>
  <div class="abs pill join"><span class="dot"><svg width="16" height="16" viewBox="0 0 16 16"><path d="M5 2l6 6-6 6" stroke="#fff" stroke-width="3" fill="none"/></svg></span>Join Us</div>
  <div class="abs pill signup"><span class="dot"><svg width="20" height="20" viewBox="0 0 20 20"><circle cx="10" cy="6" r="4.5" fill="#fff"/><path d="M2 19c0-5 4-7 8-7s8 2 8 7z" fill="#fff"/></svg></span>Sign Up</div>
  <div class="abs call-dot"><span><svg width="20" height="20" viewBox="0 0 24 24"><path d="M6.6 10.8a15 15 0 006.6 6.6l2.2-2.2c.3-.3.7-.4 1-.2 1.1.4 2.3.6 3.6.6.6 0 1 .4 1 1V20c0 .6-.4 1-1 1A17 17 0 013 4c0-.6.4-1 1-1h3.5c.6 0 1 .4 1 1 0 1.3.2 2.5.6 3.6.1.3 0 .7-.2 1z" fill="#fff"/></svg></span></div>
  <div class="abs call-top"><div class="lbl">Call Us</div><div class="num">1-800 555 0142</div></div>
  <nav class="abs nav">
    <a>HOME</a><a>ABOUT US</a><a>SERVICES</a><a>MEMBERSHIP</a><a>NEWS</a><a>RESEARCH</a><a>PROGRAMS</a><a>CONTACT US</a>
    <div class="search">SEARCH<svg width="14" height="14" viewBox="0 0 14 14"><circle cx="6" cy="6" r="4.2" stroke="#fff" stroke-width="2" fill="none"/><path d="M9 9l4 4" stroke="#fff" stroke-width="2"/></svg></div>
  </nav>
</header>

<section class="hero">
  <div class="abs hero-red" role="img" aria-label="Red camouflage backdrop"></div>
  <div class="abs hero-photo" role="img" aria-label="Smiling nurse in teal scrubs giving a thumbs up"></div>
  <h1 class="abs hero-title">LORIUM IPSUM</h1>
  <p class="abs hero-text">Vitae risus nulla aenean ut accumsan. Nostra lectus purus inceptos vestibulum pellentesque neque nulla sollicitudin pede neque sapien.</p>
  <div class="abs btn donate">DONATE NOW</div>
  <svg class="abs arrows" width="80" height="50" viewBox="0 0 80 50"><path d="M22 4L6 25l16 21M58 4l16 21-16 21" stroke="#fff" stroke-width="3" fill="none"/></svg>
</section>

<section class="abs members">
  <div class="title">Membership categories</div>
  <div class="divider"></div>
  <div class="tier" style="left:543px"><div class="n">PROVIDER</div><div class="p">$135</div></div>
  <div class="tier" style="left:714px"><div class="n">STUDENT</div><div class="p">$55</div></div>
  <div class="tier" style="left:895px;top:12px"><div class="n">RETIRED AND<br>ORGANIZATION</div><div class="p">$100</div></div>
  <svg class="abs" style="left:990px;top:38px" width="24" height="42" viewBox="0 0 24 42"><path d="M3 3l18 18L3 39" stroke="#fff" stroke-width="3" fill="none"/></svg>
</section>

<section class="welcome">
  <h2 class="abs sec-title" style="top:866px">WELCOME TO HARBORWELL NET</h2>
  <p class="abs sec-text" style="top:943px">Aliquam molestie, mi et imperdiet euismod, dui purus auctor tellus, et interdum lacus lectus et ante. Sed accumsan sollicitudin sapien, sit amet adipiscing turpis gravida ac. In congue, neque ac lobortis volutpat, libero mauris varius mi, vitae suscipit ipsum ligula vitae risus. Duis aliquam nibh a dui iaculis viverra id a velit. Vivamus egestas risus in magna varius commodo.</p>
  <div class="abs btn small-btn" style="left:539px;top:1044px;width:122px">READ MORE</div>
</section>

<section class="veteran">
  <div class="abs veteran-bg" role="img" aria-label="Dimmed group of service members in uniform"></div>
  <h2 class="abs sec-title" style="top:1172px">VETERAN'S PORTAL</h2>
  <p class="abs sec-text" style="top:1249px">Aliquam molestie, mi et imperdiet euismod, dui purus auctor tellus, et interdum lacus lectus et ante. Sed accumsan sollicitudin sapien, sit amet adipiscing turpis gravida ac. In congue, neque ac lobortis volutpat, libero mauris varius mi, vitae suscipit ipsum ligula vitae risus. Duis aliquam nibh a dui iaculis viverra id a velit. Vivamus egestas risus in magna varius commodo.</p>
  <div class="abs btn small-btn" style="left:517px;top:1340px;width:166px">JOIN VETERAN'S</div>
</section>

<section class="updates">
  <div class="abs white-sec"></div>
  <h3 class="abs col-title" style="left:72px;top:1490px">LATEST NEWS</h3>
  <h3 class="abs col-title" style="left:620px;top:1490px">PROGRAMS</h3>
  <div class="abs news-item" style="top:1584px"><div class="date"><span class="d">09</span><span class="m">FEB</span></div><p>Penatibus vel varius. Nullam consequat tortor. Odio vitae et. Natoque sollicitudin quam eget eros cras dolor porta vestibulum.</p></div>
  <div class="abs news-item" style="top:1705px"><div class="date"><span class="d">09</span><span class="m">FEB</span></div><p>Penatibus vel varius. Nullam consequat tortor. Odio vitae et. Natoque sollicitudin quam eget eros cras dolor porta vestibulum.</p></div>
  <div class="abs news-item" style="top:1826px"><div class="date"><span class="d">09</span><span class="m">FEB</span></div><p>Penatibus vel varius. Nullam consequat tortor. Odio vitae et. Natoque sollicitudin quam eget eros cras dolor porta vestibulum.</p></div>
  <div class="abs btn small-btn" style="left:78px;top:1954px;width:162px">VIEW MORE NEWS</div>
  <div class="abs prog-photo" role="img" aria-label="Doctor in a white coat talking with an older patient"></div>
  <p class="abs prog-text">Penatibus vel varius. Nullam consequat tortor. Odio vitae et. Natoque sollicitudin quam eget eros cras dolor porta vestibulum.</p>
  <div class="abs btn small-btn" style="left:619px;top:1954px;width:124px">READ MORE</div>
</section>

<footer>
  <div class="abs contact-band">
    <div class="abs" style="left:164px;top:24px;font-family:'Oswald',sans-serif;font-size:28px;font-weight:500">CONTACT US</div>
    <svg class="abs" style="left:461px;top:28px" width="22" height="30" viewBox="0 0 22 30"><path d="M11 0a11 11 0 0111 11c0 8-11 19-11 19S0 19 0 11A11 11 0 0111 0z" fill="#fff"/><circle cx="11" cy="11" r="4" fill="#516826"/></svg>
    <div class="abs" style="left:514px;top:22px;font-size:18px;line-height:22px">#123 Lorium ipsum Dolor.<br>Amit sed. AU - 6789</div>
    <svg class="abs" style="left:797px;top:32px" width="24" height="24" viewBox="0 0 24 24"><path d="M6.6 10.8a15 15 0 006.6 6.6l2.2-2.2c.3-.3.7-.4 1-.2 1.1.4 2.3.6 3.6.6.6 0 1 .4 1 1V20c0 .6-.4 1-1 1A17 17 0 013 4c0-.6.4-1 1-1h3.5c.6 0 1 .4 1 1 0 1.3.2 2.5.6 3.6.1.3 0 .7-.2 1z" fill="#fff"/></svg>
    <div class="abs" style="left:846px;top:14px;font-size:18px">Call Us</div>
    <div class="abs" style="left:846px;top:36px;font-size:28px">1-800 555 0187</div>
  </div>
  <div class="abs footer"></div>
  <div class="abs foot-nav"><span>HOME</span><span>ABOUT US</span><span>SERVICES</span><span>MEMBERSHIP</span><span>NEWS</span><span>RESEARCH</span><span>PROGRAMS</span><span>CONTACT US</span></div>
  <div class="abs social"><span></span><span></span><span></span><span></span><span></span></div>
  <div class="abs copy">Copyright © 2018. Company Name .All Right Reserved &nbsp;|&nbsp; Privacy Policy &nbsp;|&nbsp; Terms</div>
  <div class="abs foot-logo">HARBORWELL NET</div>
  <div class="abs foot-mark">M1</div>
</footer>
</body>
</html>
```